Before the kettle boils, pocast with content in its majority of technology

Page dedicated to a pocast with content in its majority of technology. The page also contains the chapters of the podcast (pluggin vocalink) will also contain news. Preferably Worpress. There is already a very basic page with a simple theme, the logo and little more, I would like something more professional. Www.lamparadebolsillo.com The logo does not want to change.

Target Market(s)

Anyone

Colors

Designer to choose colors to be used in the design.

Requirements
Must have
• You can put the vocalink pluggin with the podcast chapters

```html
<!DOCTYPE html>
<html lang="es">
<head>
<meta charset="utf-8">
<title>Before the kettle boils — podcast</title>
<link href="https://fonts.googleapis.com/css2?family=Roboto:wght@400;500;700&display=swap" rel="stylesheet">
<style>
:root{
  --bg:#1f1f1f;
  --bg-deep:#151515;
  --orange:#f07b1a;
  --orange-light:#f7a23a;
  --card:#ffffff;
  --card-head:#f2f2f2;
  --line:#e3e3e3;
  --text:#555555;
  --title:#222222;
  --muted:#8a8a8a;
  --player:#f4f4f4;
}
*{box-sizing:border-box;margin:0;padding:0}
html,body{width:1200px;height:3629px;overflow:hidden}
body{background:var(--bg);font-family:'Roboto',sans-serif;color:var(--text);position:relative}

/* header */
.site-header{position:absolute;left:0;top:0;width:1200px;height:180px;
  background:radial-gradient(ellipse at 72% 40%,#3a3a3a 0%,#262626 35%,#1c1c1c 70%);}
.brand{position:absolute;left:140px;top:30px;display:flex;align-items:center;gap:14px}
.brand-dot{width:70px;height:70px;border-radius:50%;background:var(--orange)}
.brand-name{font-size:22px;font-weight:700;color:var(--orange);text-transform:uppercase;letter-spacing:.5px;width:220px;line-height:1.15}
.social-top{position:absolute;left:962px;top:22px;display:flex;gap:8px}
.social-top span{width:36px;height:36px;border-radius:50%;border:2px solid #e6e6e6}
.auth{position:absolute;top:84px;left:893px;display:flex;gap:12px}
.auth a{display:block;height:34px;line-height:34px;font-size:11px;font-weight:700;color:#fff;text-decoration:none;text-align:center;border-radius:2px}
.auth .register{width:88px;border:1px solid #aaa}
.auth .login{width:88px;background:var(--orange)}

/* cards */
.card{position:absolute;background:var(--card);display:flex;flex-direction:column;border-radius:2px;overflow:hidden}
.card-head{background:var(--card-head);padding:18px 26px 14px;border-bottom:1px solid var(--line)}
.card-title{font-size:20px;font-weight:500;color:var(--title);line-height:1.25}
.meta{display:flex;gap:22px;font-size:12px;color:var(--muted);margin-top:12px;align-items:center}
.meta .author{color:var(--orange)}
.meta i{display:inline-block;width:10px;height:10px;background:#aaa;border-radius:2px;margin-right:7px;vertical-align:-1px}
.card-body{padding:22px 26px 0;font-size:13.5px;line-height:1.5}
.more{color:var(--orange);font-weight:700}
.card-foot{margin-top:auto;padding:0 26px 16px}
.share-row{display:flex;align-items:center;justify-content:space-between;border-top:1px solid var(--line);padding-top:14px}
.share{display:flex;align-items:center;gap:10px;font-size:11px;font-weight:700;color:#333}
.share b{width:26px;height:26px;border-radius:50%;border:1px solid #bbb;display:flex;align-items:center;justify-content:center}
.posted{font-size:11px;color:var(--muted)}
.card-foot .posted.below{margin-top:12px}
.share-icons{display:flex;gap:6px;align-items:center}
.share-icons span{width:22px;height:22px;border-radius:50%;background:#9aa3ad}
.share-icons .first{width:26px;height:26px;border:1px solid #bbb;background:#fff;margin-right:4px}

/* player */
.player{display:flex;background:var(--player);border:1px solid #e6e6e6;margin-top:16px}
.player-main{flex:1;position:relative;padding:10px}
.play{border-radius:50%;background:#f6b91a;position:absolute}
.play::after{content:"";position:absolute;left:40%;top:30%;border-left:12px solid #fff;border-top:8px solid transparent;border-bottom:8px solid transparent}
.p-title{position:absolute;color:#333}
.p-brand{position:absolute;font-weight:700;color:#333}
.wave{position:absolute;left:10px;right:10px;bottom:8px;
  background:repeating-linear-gradient(90deg,#bdbdbd 0 2px,transparent 2px 4px);
  -webkit-mask:linear-gradient(0deg,#000 30%,rgba(0,0,0,.4) 100%);}
.p-time{position:absolute;color:#666}
.cover{flex:none}
.player.sm{height:98px}
.player.sm .play{left:8px;top:10px;width:32px;height:32px}
.player.sm .play::after{border-left-width:9px;border-top-width:6px;border-bottom-width:6px}
.player.sm .p-title{left:48px;top:10px;font-size:8px;width:80px}
.player.sm .p-brand{right:8px;top:8px;font-size:7px}
.player.sm .wave{height:24px}
.player.sm .cover{width:96px}
.player.lg{height:220px;margin-top:20px}
.player.lg .play{left:14px;top:14px;width:72px;height:72px}
.player.lg .play::after{border-left-width:22px;border-top-width:14px;border-bottom-width:14px}
.player.lg .p-title{left:100px;top:22px;font-size:19px;line-height:1.3;width:260px}
.player.lg .p-brand{right:14px;top:14px;font-size:14px}
.player.lg .wave{height:70px;left:14px;right:14px}
.player.lg .p-time{top:112px;font-size:12px}
.player.lg .cover{width:218px}
.icons-row{position:absolute;display:flex;gap:14px}
.icons-row span{background:#333;border-radius:50%}
.player.dark{background:#111;border-color:#111}
.player.dark .p-title,.player.dark .p-brand,.player.dark .p-time{color:#fff}

/* sidebar */
.widget{position:absolute;left:866px;width:223px;background:#fff;border:3px solid var(--orange);border-radius:2px}
.widget.search{border:none;padding:18px 20px;height:67px}
.search input{width:100%;height:32px;border:1px solid #ccc;font:12px 'Roboto',sans-serif;padding:0 8px;color:#999}
.widget h3{height:50px;line-height:50px;padding-left:20px;font-size:17px;font-weight:500;color:#fff;background:linear-gradient(180deg,var(--orange-light),var(--orange))}
.widget ul{list-style:none;padding:6px 20px}
.widget li{font-size:12px;color:#444;border-bottom:1px solid #ececec;padding:12px 0;line-height:1.4}
.widget li:last-child{border-bottom:none}
.contact li::before{content:"";display:inline-block;width:10px;height:10px;background:#777;border-radius:2px;margin-right:10px}
.archives li{padding:10px 0}
.archives li::before{content:"›";color:#999;margin-right:10px}

/* pagination */
.pager{position:absolute;top:3380px;left:111px;width:729px;display:flex;justify-content:center;gap:8px}
.pager span{height:30px;min-width:30px;border-radius:15px;border:1px solid #444;color:#ccc;font-size:11px;display:flex;align-items:center;justify-content:center;padding:0 10px}
.pager .active{background:var(--orange);border-color:var(--orange);color:#fff}

/* footer */
.site-footer{position:absolute;left:0;top:3462px;width:1200px;height:167px;background:var(--bg-deep);border-top:1px solid #333;text-align:center}
.foot-social{display:flex;justify-content:center;gap:8px;margin-top:46px}
.foot-social span{width:34px;height:34px;border-radius:50%;border:2px solid #556}
.copy{font-size:11px;color:#888;margin-top:14px}
.foot-links{font-size:11px;color:#888;margin-top:6px}
</style>
</head>
<body>

<header class="site-header" role="img" aria-label="Dark header backdrop with a studio microphone photo">
  <div class="brand"><span class="brand-dot"></span><span class="brand-name">Before the kettle boils</span></div>
  <div class="social-top"><span></span><span></span><span></span></div>
  <div class="auth"><a class="register" href="#">REGISTER</a><a class="login" href="#">LOGIN</a></div>
</header>

<!-- post: cambio de logo -->
<article class="card" style="left:111px;top:194px;width:729px;height:285px">
  <div class="card-head">
    <h2 class="card-title">Cambio de logo</h2>
    <div class="meta"><span class="author"><i></i>De Tolvan</span><span><i></i>19 May, 2017</span><span><i></i>20</span></div>
  </div>
  <div class="card-body">Hola a Tod@s!<br>¿Salta a la vista no?, pues sí, renovamos diseño del logo y algo en la web. Aquí los cambios irán poco a poco pero procuraré dejar todo lo que quiero modificar hecho en una semana como mucho, todo dependerá del tiempo que le pueda dedicar aunque lo difícil ya está hecho...<span class="more">[Lee Mas]</span></div>
  <div class="card-foot"><div class="share-row">
    <div class="share-icons"><span class="first"></span><span></span><span></span><span></span><span></span><span></span><span></span><span></span><span></span><span></span><span></span></div>
    <span class="posted">Publicado en Sin categoría | Deja un comentario</span>
  </div></div>
</article>

<!-- row 2 -->
<article class="card" style="left:111px;top:508px;width:351px;height:467px">
  <div class="card-head">
    <h2 class="card-title">¿Te gustan las series?¿Conoces seriesbox.tv?</h2>
    <div class="meta"><span class="author"><i></i>De Tolvan</span><span><i></i>17 May, 2017</span><span><i></i>20</span></div>
  </div>
  <div class="card-body">Hola a Tod@s!<br>¿Salta a la vista no?, pues sí, renovamos diseño del logo y algo en la web. Aquí los cambios irán poco a poco pero procuraré dejar todo lo que quiero modificar hecho en una sem...<span class="more">[Lee Mas]</span>
    <div class="player sm"><div class="player-main"><span class="play"></span><span class="p-title">¿Te gustan las series?¿Conoces seriesbox.tv?</span><span class="p-brand">vocalink</span><span class="wave"></span></div><div class="cover" role="img" aria-label="Episode cover: collage of series posters" style="background:linear-gradient(135deg,#3b2a4a,#1b1b2b 60%,#6b3020)"></div></div>
  </div>
  <div class="card-foot"><div class="share-row"><span class="share"><b>↪</b>COMPARTE</span></div><p class="posted below">Publicado en Sin categoría | Deja un comentario</p></div>
</article>

<article class="card" style="left:486px;top:508px;width:354px;height:467px">
  <div class="card-head">
    <h2 class="card-title">Un anuncio y una prueba</h2>
    <div class="meta"><span class="author"><i></i>De Tolvan</span><span><i></i>13 May, 2017</span><span><i></i>20</span></div>
  </div>
  <div class="card-body">Hola a tod@s!!<br>Sí, lo sé ha vuelto a pasar, mucho tiempo desde la última publicación. Esto lo tengo muy abandonado y no hay excusa, me da pena pero es cierto por gandulería o por...<span class="more">[Lee Mas]</span>
    <div class="player sm"><div class="player-main"><span class="play"></span><span class="p-title">Un anuncio y una prueba</span><span class="p-brand">vocalink</span><span class="wave"></span></div><div class="cover" role="img" aria-label="Episode cover: round black badge artwork" style="background:radial-gradient(circle,#444 0 40%,#111 42% 62%,#fff 64%)"></div></div>
  </div>
  <div class="card-foot"><div class="share-row"><span class="share"><b>↪</b>COMPARTE</span></div><p class="posted below">Publicado en Sin categoría | Deja un comentario</p></div>
</article>

<!-- seguridad -->
<article class="card" style="left:111px;top:1004px;width:729px;height:533px">
  <div class="card-head">
    <h2 class="card-title">Seguridad en tu Mail</h2>
    <div class="meta"><span class="author"><i></i>De Tolvan</span><span><i></i>23 Nov, 2016</span><span><i></i>20</span></div>
  </div>
  <div class="card-body">¡Hola a todos!<br>Hoy poco más que decir por aquí de los dicho en el podcast. Para aquellos que necesiten un punto más de seguridad en el correo electrónico esta VaultMail. Planes gratuitos y de pago, codificación, mensajes que se pueden auto destruir, etc...<span class="more">[Lee Mas]</span>
    <div class="player lg"><div class="player-main"><span class="play"></span><span class="p-title">Seguridad en tu Mail</span><span class="p-brand">vocalink</span><span class="p-time" style="left:14px">00:00</span><span class="p-time" style="right:14px">09:53</span><span class="wave"></span></div><div class="cover" role="img" aria-label="Episode cover: mail app artwork on navy" style="background:linear-gradient(160deg,#3b3f8a,#2b2e6c)"></div></div>
  </div>
  <div class="card-foot" style="margin-top:auto"><div class="share-row"><span class="share"><b>↪</b>COMPARTE</span><span class="posted">Publicado en Sin categoría | Deja un comentario</span></div></div>
</article>

<!-- row 4 -->
<article class="card" style="left:111px;top:1563px;width:351px;height:465px">
  <div class="card-head">
    <h2 class="card-title">Kumo Tab2, calidad precio insuperable</h2>
    <div class="meta"><span class="author"><i></i>De Tolvan</span><span><i></i>20 Nov, 2016</span><span><i></i>20</span></div>
  </div>
  <div class="card-body">¡Hola a todos!<br>Con un poco de retraso publicamos el post del podcast de la tableta de Kumo. Tableta que como viene siendo habitual de la marca china, da mucho más de lo que cuesta....<span class="more">[Lee Mas]</span>
    <div class="player sm"><div class="player-main"><span class="play"></span><span class="p-title">Kumo Tab2, calidad precio insuperable</span><span class="p-brand">vocalink</span><span class="wave"></span></div><div class="cover" role="img" aria-label="Episode cover: orange brand artwork" style="background:var(--orange)"></div></div>
  </div>
  <div class="card-foot"><div class="share-row"><span class="share"><b>↪</b>COMPARTE</span></div><p class="posted below">Publicado en Sin categoría | Deja un comentario</p></div>
</article>

<article class="card" style="left:486px;top:1563px;width:354px;height:465px">
  <div class="card-head">
    <h2 class="card-title">Notaria, así lo hago yo</h2>
    <div class="meta"><span class="author"><i></i>De Tolvan</span><span><i></i>26 Oct, 2016</span><span><i></i>20</span></div>
  </div>
  <div class="card-body">En este podcast os hablo de mi uso particular de Notaria, con pros y contras, como organizo, etc. Intentaré hacer por aquí un resumen de lo comentado en el podcast.Yo soy un usuario muy activo desde hace tiempo...<span class="more">[Lee Mas]</span>
    <div class="player sm"><div class="player-main"><span class="play"></span><span class="p-title">Notaria, así lo hago yo</span><span class="p-brand">vocalink</span><span class="wave"></span></div><div class="cover" role="img" aria-label="Episode cover: green app artwork" style="background:#3fae3a"></div></div>
  </div>
  <div class="card-foot"><div class="share-row"><span class="share"><b>↪</b>COMPARTE</span></div><p class="posted below">Publicado en Sin categoría | Deja un comentario</p></div>
</article>

<!-- quillon -->
<article class="card" style="left:111px;top:2059px;width:729px;height:342px">
  <div class="card-head">
    <h2 class="card-title">Quillon</h2>
    <div class="meta"><span class="author"><i></i>De Tolvan</span><span><i></i>30 Jul, 2016</span><span><i></i>20</span></div>
  </div>
  <div class="card-body">Hola a todos<br>Seguramente el siguiente post de este blog ya podrá ser importado directamente desde Quillon, mi editor de texto favorito.<br><br>La actualización la anuncian para el día 3, veremos a ver<br><br>un saludo</div>
  <div class="card-foot"><div class="share-row"><span class="share"><b>↪</b>COMPARTE</span><span class="posted">Publicado en Sin categoría | Deja un comentario</span></div></div>
</article>

<!-- row 6 -->
<article class="card" style="left:111px;top:2432px;width:351px;height:334px">
  <div class="card-head">
    <h2 class="card-title">Un sonora gratuito para mOS</h2>
    <div class="meta"><span class="author"><i></i>De Tolvan</span><span><i></i>26 Jul, 2016</span><span><i></i>20</span></div>
  </div>
  <div class="card-body">Buenas tardes!<br>Os añado un entrada en el blog que no se si tratará en podcast, imagino que no y así solo seréis vosotros, los que visitáis el blog quienes tendréis acceso a este tipo ....<span class="more">[Lee Mas]</span></div>
  <div class="card-foot"><div class="share-row"><span class="share"><b>↪</b>COMPARTE</span></div><p class="posted below">Publicado en Sin categoría | Deja un comentario</p></div>
</article>

<article class="card" style="left:486px;top:2432px;width:354px;height:334px">
  <div class="card-head">
    <h2 class="card-title">¿Alternativa a Notaria?</h2>
    <div class="meta"><span class="author"><i></i>De Tolvan</span><span><i></i>10 Jul, 2016</span><span><i></i>20</span></div>
  </div>
  <div class="card-body">Después de casi un mes ausente de estos lares, vuelvo con un tema que estaba preparando desde hace un tiempo y más de uno me habéis solicitado por correo electrónico y redes sociales. En boca (y teclado) de tod...<span class="more">[Lee Mas]</span></div>
  <div class="card-foot"><div class="share-row"><span class="share"><b>↪</b>COMPARTE</span></div><p class="posted below">Publicado en Sin categoría | Deja un comentario</p></div>
</article>

<!-- podcast futuros -->
<article class="card" style="left:111px;top:2793px;width:729px;height:535px">
  <div class="card-head">
    <h2 class="card-title">Podcast futuros, vocalink, seriere recomendada</h2>
    <div class="meta"><span class="author"><i></i>De Tolvan</span><span><i></i>26 Jul, 2016</span><span><i></i>20</span></div>
  </div>
  <div class="card-body">Podcast de hoy variado, un adelanto de uno o una serie (ya veremos) de podcast que voy a grabar en un futuro, opinión de los nuevos planes de precios de vocalink y la recomocomendación de una serie The Remnants. Como ya os comento en el podcast el tema Notaria está ya muy adelantado, solo falta determinar el formato, uno más largo 2 cortos, uno a cada aplicación... Ya veremos....<span class="more">[Lee Mas]</span>
    <div class="player lg dark"><div class="player-main"><span class="play"></span><span class="p-title">Podcast futuros, vocalink, serie recomendada</span><span class="p-brand">vocalink</span><span class="p-time" style="left:14px">00:00</span><span class="p-time" style="right:14px">13:20</span><span class="wave"></span></div><div class="cover" role="img" aria-label="Episode cover: underwater photo in deep blue tones" style="background:linear-gradient(160deg,#2e7fa0,#0e2f4a)"></div></div>
  </div>
  <div class="card-foot"><div class="share-row"><span class="share"><b>↪</b>COMPARTE</span><span class="posted">Publicado en Sin categoría | Deja un comentario</span></div></div>
</article>

<nav class="pager"><span>« Prev</span><span class="active">01</span><span>02</span><span>03</span><span>05</span><span>06</span><span>Next »</span></nav>

<!-- sidebar -->
<aside>
  <div class="widget search" style="top:194px"><input type="text" value="Buscar..." aria-label="Buscar"></div>
  <div class="widget" style="top:298px;height:307px">
    <h3>Recent Posts</h3>
    <ul><li>Cambio de logo</li><li>¿Te gustan las series?¿Conoces seriesbox.tv?</li><li>Un anuncio y una prueba</li><li>Seguridad en tu Mail</li><li>Kumo Tab2, calidad precio insuperable</li></ul>
  </div>
  <div class="widget contact" style="top:634px;height:242px">
    <h3>Contacto</h3>
    <ul><li>Chirpline</li><li>vocalink</li><li>Audiobay</li><li>Mail</li></ul>
  </div>
  <div class="widget archives" style="top:903px;height:762px">
    <h3>Archives</h3>
    <ul><li>May 2017</li><li>April 2017</li><li>March 2017</li><li>February 2017</li><li>January 2017</li><li>December 2016</li><li>November 2016</li><li>October 2016</li><li>September 2017</li><li>August 2017</li><li>July 2016</li><li>June 2016</li><li>May 2016</li><li>April 2016</li><li>March 2016</li><li>February 2016</li><li>January 2016</li></ul>
  </div>
</aside>

<footer class="site-footer">
  <div class="foot-social"><span></span><span></span><span></span></div>
  <p class="copy">Copyright © 2017 Before the kettle boils. All Rights Reserved.</p>
  <p class="foot-links">Terms of Use | Privacy Policy | Sitemap</p>
</footer>

</body>
</html>
```